KPL Construction we build lodges in Botswana

We need a Design Layout only with Categories where we can update each projects photos.... We have a web address and a host - kpl.construction

```html
<!DOCTYPE html>
<html lang="en">
<head>
<meta charset="utf-8">
<title>KPL Construction</title>
<link href="https://fonts.googleapis.com/css2?family=Raleway:wght@400;500;600;700&family=Open+Sans:wght@400;600&display=swap" rel="stylesheet">
<style>
  :root {
    --red: #e2533b;
    --red-dark: #c9432d;
    --red-band: #e4553f;
    --ink: #222222;
    --text: #444444;
    --muted: #666666;
    --white: #ffffff;
    --footer: #1e1e1e;
    --footer-text: #bbbbbb;
  }
  * { box-sizing: border-box; margin: 0; padding: 0; }
  html, body { width: 1200px; height: 2769px; overflow: hidden; background: var(--white); }
  body { font-family: "Open Sans", Arial, sans-serif; color: var(--text); }
  .page { position: relative; width: 1200px; height: 2769px; overflow: hidden; }

  /* Header */
  .site-header { position: absolute; top: 0; left: 0; width: 1200px; height: 72px; background: var(--white); }
  .brand { position: absolute; left: 144px; top: 16px; font-family: "Raleway", Arial, sans-serif; font-weight: 500; font-size: 31px; color: var(--red); letter-spacing: 0.2px; }
  .main-nav { position: absolute; right: 144px; top: 24px; display: flex; gap: 37px; font-family: "Raleway", Arial, sans-serif; font-size: 17px; }
  .main-nav a { color: #444; text-decoration: none; }
  .main-nav a.active { color: var(--red); }

  /* Hero */
  .hero { position: absolute; top: 72px; left: 0; width: 1200px; height: 543px; }
  .hero-photo { position: absolute; inset: 0; background: linear-gradient(180deg, #a9acaf 0%, #c7c8c6 30%, #9a968c 52%, #7e7a68 66%, #8d8a4e 76%, #b0925a 88%, #9a7a45 100%); }
  .hero-title { position: absolute; top: 68px; width: 100%; text-align: center; font-family: "Raleway", Arial, sans-serif; font-weight: 700; font-size: 32px; line-height: 40px; color: var(--ink); }
  .btn { display: inline-block; font-family: "Raleway", Arial, sans-serif; font-size: 15px; text-decoration: none; text-align: center; }
  .hero .btn { position: absolute; left: 545px; top: 161px; width: 110px; height: 44px; line-height: 44px; background: var(--white); color: var(--red); border-radius: 2px; }
  .slider-arrow { position: absolute; width: 34px; height: 34px; }
  .hero .arrow-left { left: 46px; top: 253px; }
  .hero .arrow-right { left: 1117px; top: 253px; }

  /* Welcome */
  .welcome { position: absolute; top: 615px; left: 0; width: 1200px; height: 374px; text-align: center; }
  .section-title { font-family: "Raleway", Arial, sans-serif; font-weight: 700; font-size: 32px; color: var(--red); }
  .welcome .section-title { position: absolute; top: 80px; width: 100%; }
  .welcome p { position: absolute; left: 120px; top: 124px; width: 960px; font-size: 12.5px; line-height: 24px; color: var(--text); white-space: nowrap; }
  .btn-outline { border: 1.5px solid var(--red); color: var(--red); background: var(--white); border-radius: 2px; width: 110px; height: 43px; line-height: 40px; }
  .welcome .btn { position: absolute; left: 545px; top: 211px; }

  .connector { position: absolute; left: 598px; width: 4px; height: 78px; background: var(--ink); z-index: 3; }
  .connector.light { background: var(--white); }

  /* Categories */
  .categories { position: absolute; top: 989px; left: 0; width: 1200px; height: 434px; color: var(--white); }
  .band-photo { position: absolute; inset: 0; background: linear-gradient(160deg, #e9634d 0%, #e2533b 45%, #d84b35 75%, #df5640 100%); }
  .categories .ghost-title { position: absolute; top: 40px; width: 100%; text-align: center; font-family: "Raleway", Arial, sans-serif; font-weight: 700; font-size: 30px; color: rgba(255,255,255,0.12); }
  .category { position: absolute; top: 113px; width: 290px; text-align: center; }
  .category .icon { width: 144px; height: 144px; border-radius: 50%; background: var(--white); margin: 0 auto; display: flex; align-items: center; justify-content: center; }
  .category h3 { margin-top: 11px; font-family: "Raleway", Arial, sans-serif; font-weight: 600; font-size: 24px; }
  .category p { margin-top: 8px; font-size: 11px; line-height: 17px; font-weight: 600; }
  .categories .arrow-left { left: 50px; top: 215px; }
  .categories .arrow-right { left: 1120px; top: 215px; }

  /* Projects */
  .projects { position: absolute; top: 1423px; left: 0; width: 1200px; height: 713px; }
  .projects .section-title { position: absolute; top: 116px; width: 100%; text-align: center; }
  .project-grid { position: absolute; left: 144px; top: 177px; width: 912px; height: 337px; display: grid; grid-template-columns: 218px 218px 218px 218px; grid-template-rows: 159px 159px; column-gap: 13px; row-gap: 19px; }
  .project-photo { width: 100%; height: 100%; }
  .p-lodge { background: linear-gradient(180deg, #4d6b3a, #c9c3b4 55%, #3f5a2c); }
  .p-apartments { grid-row: 1 / 3; grid-column: 2; background: linear-gradient(180deg, #c9b48a, #8a8f86 50%, #4e7a3c); }
  .p-roundhouse { background: linear-gradient(180deg, #7fb0dc, #5e8a60 55%, #7a5a3a); }
  .p-treehouse { background: linear-gradient(180deg, #4c8fd0, #8e7254 55%, #c8b89a); }
  .p-cottage { background: linear-gradient(180deg, #4a6a34, #b36a4a 45%, #cfcabd 65%, #4f7c2e); }
  .p-pool { grid-column: 3 / 5; background: linear-gradient(90deg, #2b2620, #6e5532 45%, #c98e3e 70%, #3a3026); }
  .projects .btn { position: absolute; left: 545px; top: 549px; }

  /* Contact */
  .contact { position: absolute; top: 2136px; left: 0; width: 1200px; height: 473px; color: var(--white); }
  .contact .band-photo { background: linear-gradient(180deg, #e4553f 0%, #e2533b 55%, #d14631 100%); }
  .contact .section-title { position: absolute; top: 78px; width: 100%; text-align: center; color: var(--white); }
  .contact-form .field { position: absolute; background: var(--white); color: #333; font-size: 12px; padding: 11px 14px; }
  .field-name { left: 375px; top: 144px; width: 216px; height: 42px; }
  .field-email { left: 607px; top: 144px; width: 216px; height: 42px; }
  .field-message { left: 375px; top: 201px; width: 448px; height: 120px; }
  .btn-submit { position: absolute; left: 546px; top: 340px; width: 106px; height: 44px; line-height: 44px; background: var(--ink); color: var(--white); font-family: "Raleway", Arial, sans-serif; font-size: 15px; text-align: center; letter-spacing: 0.5px; }

  /* Footer */
  .site-footer { position: absolute; top: 2609px; left: 0; width: 1200px; height: 160px; background: var(--footer); color: var(--footer-text); font-size: 12px; }
  .footer-nav { position: absolute; left: 144px; top: 71px; }
  .footer-nav a { color: var(--footer-text); text-decoration: none; }
  .footer-nav span { margin: 0 8px; }
  .copyright { position: absolute; left: 144px; top: 102px; }
  .social { position: absolute; left: 1003px; top: 88px; display: flex; gap: 22px; }
  .social span { width: 14px; height: 14px; border-radius: 50%; background: #cccccc; display: block; }
</style>
</head>
<body>
<div class="page">

  <header class="site-header">
    <div class="brand">KPL Construction</div>
    <nav class="main-nav">
      <a class="active" href="#">Home</a>
      <a href="#">Categories</a>
      <a href="#">Projects</a>
      <a href="#">About</a>
      <a href="#">Contact</a>
    </nav>
  </header>

  <section class="hero">
    <div class="hero-photo" role="img" aria-label="Photo of a city skyline with modern buildings under a cloudy sky, with grassland in the foreground"></div>
    <h1 class="hero-title">We are a construction company.<br>We build lodges in Botswana.</h1>
    <a class="btn" href="#">Read more</a>
    <svg class="slider-arrow arrow-left" viewBox="0 0 34 34"><circle cx="17" cy="17" r="15" fill="#fff" stroke="#333" stroke-width="2"/><path d="M19.5 10.5 13 17l6.5 6.5" fill="none" stroke="#333" stroke-width="3"/></svg>
    <svg class="slider-arrow arrow-right" viewBox="0 0 34 34"><circle cx="17" cy="17" r="15" fill="#fff" stroke="#333" stroke-width="2"/><path d="M14.5 10.5 21 17l-6.5 6.5" fill="none" stroke="#333" stroke-width="3"/></svg>
  </section>

  <section class="welcome">
    <h2 class="section-title">Welcome to KPL Construction</h2>
    <p>Nam tempus, quam in bibendum vulputate, sapien dolor viverra nisl, vitae euismod elit turpis et nulla. Aliquam erat volutpat. Pellentesque blandit lacus<br>eget nunc faucibus, et tincidunt eros viverra. Phasellus consequat sagittis nisi suscipit feugiat. Cras eget leo sed nunc hendrerit ultricies eu at nisl.<br>Praesent iaculis faucibus urna sit amet lacinia. Maecenas consequat justo enim, ac mattis massa imperdiet quis.</p>
    <a class="btn btn-outline" href="#">Read more</a>
  </section>

  <div class="connector" style="top:951px;"></div>

  <section class="categories">
    <div class="band-photo" role="img" aria-label="Construction site with cranes and scaffolding under a red colour overlay"></div>
    <div class="ghost-title">Categories</div>

    <article class="category" style="left:141px;">
      <div class="icon">
        <svg width="72" height="56" viewBox="0 0 72 56" fill="none" stroke="#e2533b" stroke-width="2.5">
          <rect x="6" y="12" width="52" height="40"/><path d="M2 12h60M62 6v46M58 6h10"/>
          <rect x="13" y="20" width="8" height="8"/><rect x="28" y="20" width="8" height="8"/><rect x="43" y="20" width="8" height="8"/>
          <rect x="13" y="34" width="8" height="8"/><rect x="43" y="34" width="8" height="8"/><path d="M28 52V36h8v16"/>
        </svg>
      </div>
      <h3>Lodges</h3>
      <p>Maecenas accumsan quam varius imperdiet vel eget elit. Aenean facilisis tincidunt lectus, id dictum nisi luctus eget. Vivamus efficitur ex condimentum.</p>
    </article>

    <article class="category" style="left:455px;">
      <div class="icon">
        <svg width="48" height="58" viewBox="0 0 48 58" fill="none" stroke="#e2533b" stroke-width="2.5">
          <path d="M4 18 24 4l20 14z"/><rect x="10" y="18" width="28" height="14"/><path d="M20 32v-8h8v8"/>
          <path d="M14 32 8 56M34 32l6 24M11 44h26M16 32l-2 24M32 32l2 24"/>
        </svg>
      </div>
      <h3>Curabitur</h3>
      <p>Maecenas accumsan quam varius imperdiet vel eget elit. Aenean facilisis tincidunt lectus, id dictum nisi luctus eget. Vivamus efficitur ex condimentum.</p>
    </article>

    <article class="category" style="left:769px;">
      <div class="icon">
        <svg width="64" height="54" viewBox="0 0 64 54" fill="none" stroke="#e2533b" stroke-width="2.5">
          <path d="M4 24 32 4l28 20"/><path d="M10 20v30h44V20"/><path d="M24 50V34h16v16"/>
          <path d="M10 30h44M10 40h14M40 40h14"/><rect x="26" y="16" width="12" height="8"/>
        </svg>
      </div>
      <h3>Tree House</h3>
      <p>Maecenas accumsan quam varius imperdiet vel eget elit. Aenean facilisis tincidunt lectus, id dictum nisi luctus eget. Vivamus efficitur ex condimentum.</p>
    </article>

    <svg class="slider-arrow arrow-left" viewBox="0 0 34 34"><path d="M21 6 10 17l11 11" fill="none" stroke="#fff" stroke-width="4"/></svg>
    <svg class="slider-arrow arrow-right" viewBox="0 0 34 34"><path d="M13 6l11 11-11 11" fill="none" stroke="#fff" stroke-width="4"/></svg>
  </section>

  <div class="connector" style="top:1385px;"></div>

  <section class="projects">
    <h2 class="section-title">Our Projects</h2>
    <div class="project-grid">
      <div class="project-photo p-lodge" role="img" aria-label="Photo of a white thatched lodge among trees"></div>
      <div class="project-photo p-apartments" role="img" aria-label="Photo of a modern apartment building with balconies and palms"></div>
      <div class="project-photo p-roundhouse" role="img" aria-label="Photo of a round lodge with a green conical roof under acacia trees"></div>
      <div class="project-photo p-treehouse" role="img" aria-label="Photo of a raised wooden tree house lodge"></div>
      <div class="project-photo p-cottage" role="img" aria-label="Photo of a cottage with a red tiled roof and a lawn"></div>
      <div class="project-photo p-pool" role="img" aria-label="Photo of a lit lodge deck with a pool at dusk"></div>
    </div>
    <a class="btn btn-outline" href="#">Read more</a>
  </section>

  <div class="connector" style="top:2097px;"></div>

  <section class="contact">
    <div class="band-photo" role="img" aria-label="Apartment buildings under a red colour overlay"></div>
    <h2 class="section-title">Contact Us</h2>
    <form class="contact-form">
      <div class="field field-name">Name</div>
      <div class="field field-email">Email</div>
      <div class="field field-message">Message</div>
      <div class="btn-submit">SUBMIT</div>
    </form>
  </section>

  <div class="connector light" style="top:2568px;"></div>

  <footer class="site-footer">
    <nav class="footer-nav">
      <a href="#">Home</a><span>|</span><a href="#">Categories</a><span>|</span><a href="#">Projects</a><span>|</span><a href="#">About</a><span>|</span><a href="#">Contact</a>
    </nav>
    <div class="copyright">Copyright &copy; 2019 &nbsp;KPL Construction. &nbsp;&nbsp;All rights reserved.</div>
    <div class="social" aria-label="Social links"><span></span><span></span></div>
  </footer>

</div>
</body>
</html>
```